Experienced and Professional Marriage Celebrant

I need a web design for my services as a marriage celebrant in the Sydney area. I want people to have the impression I am a modern and professional marriage celebrant who can tailor a wedding ceremony and execute the ceremony with a high level of care and accommodate and adapt to any style of wedding and personalities of couples. I like a mint and pink and black theme and I am not sure whether to use the professional photos of me, might be too stiff! But would like to see ideas you can come up with. Happy to use other photos you might have
Updates

Project Deadline Extended
Reason: I have haven't been able to respond as quickly as I would have liked this last week to comments so extending a few days. Thanks

Industry/Entity Type

It Professional

```html
<!DOCTYPE html>
<html lang="en">
<head>
<meta charset="utf-8">
<title>Mara Linwood Celebrant</title>
<link href="https://fonts.googleapis.com/css2?family=Arimo:wght@400;700&display=swap" rel="stylesheet">
<style>
:root{
  --purple:#7b3596;
  --purple-dark:#5e2474;
  --purple-light:#9a5cb1;
  --ink:#111;
  --muted:#8a8a8a;
  --link:#2b2b8c;
  --panel-top:#ffffff;
  --panel-bottom:#e9e9ec;
  --photo-sky:#a9c3d3;
  --photo-sand:#b59a74;
  --photo-dress:#d9c6cc;
  --photo-warm:#cdbfae;
  --photo-portrait:#8e6a5c;
}
*{margin:0;padding:0;box-sizing:border-box}
html,body{width:756px;height:1200px;overflow:hidden}
body{
  position:relative;
  font-family:"Arimo",Arial,sans-serif;
  color:var(--ink);
  background:
    radial-gradient(circle at 690px 90px, rgba(154,92,177,.28) 0 70px, rgba(154,92,177,0) 110px),
    radial-gradient(circle at -40px 330px, rgba(154,92,177,.35) 0 90px, rgba(154,92,177,0) 160px),
    linear-gradient(180deg,#fff 0,#fff 520px,#d6b6de 760px,#9b58b0 960px,#7d3794 1072px);
}
.abs{position:absolute}
.brand{left:0;width:756px;top:30px;text-align:center;font-size:30px;color:var(--purple);letter-spacing:.5px}
.brand-dot{display:inline-block;width:10px;height:10px;border-radius:50%;background:var(--purple);margin-right:10px;vertical-align:middle}
.nav{left:50px;top:98px;width:661px;height:34px;background:linear-gradient(180deg,var(--purple-light),var(--purple) 60%,var(--purple-dark));display:flex;padding-left:69px}
.nav a{color:#fff;text-decoration:none;font-size:18px;line-height:32px;padding:0 8px}
.nav a.active{background:rgba(255,255,255,.22);padding:0 12px}
.hero{left:50px;top:136px;width:661px;height:222px;background:linear-gradient(180deg,var(--photo-sky),var(--photo-sand));box-shadow:0 2px 4px rgba(0,0,0,.4)}
.panel{left:47px;top:372px;width:666px;height:694px;background:linear-gradient(180deg,var(--panel-top),var(--panel-bottom));box-shadow:0 0 3px rgba(0,0,0,.3)}
h2{position:absolute;font-weight:400;font-size:22px}
.rule{position:absolute;height:2px;background:var(--purple)}
.body-text{position:absolute;font-size:18.3px;line-height:22px}
.photo{position:absolute}
.welcome-photo{left:576px;top:411px;width:127px;height:191px;background:var(--photo-dress)}
.services-photo{left:64px;top:681px;width:83px;height:125px;background:var(--photo-warm)}
.read-more{color:var(--link);text-decoration:none}
.avatar{position:absolute;width:84px;height:84px;border-radius:50%;background:var(--photo-portrait);box-shadow:0 1px 3px rgba(0,0,0,.5)}
.client{position:absolute;font-size:11px;width:84px;text-align:center}
.quote{position:absolute;font-size:11px;line-height:13px;color:var(--muted);width:210px}
.footer{left:0;top:1072px;width:756px;height:128px;background:repeating-linear-gradient(135deg,#1e1e1e 0 2px,#151515 2px 4px)}
.footer-col{position:absolute;top:1090px;color:#fff;font-size:13px;line-height:16.5px;list-style:none}
.social{position:absolute;top:1110px;left:473px;display:flex;gap:3px}
.social span{width:8px;height:8px;background:#9a9a9a;display:block}
</style>
</head>
<body>
<div class="abs brand"><span class="brand-dot"></span>Mara Linwood Celebrant</div>

<nav class="abs nav">
  <a class="active" href="#">Home</a><a href="#">About</a><a href="#">Ceremony</a><a href="#">Gallery</a><a href="#">Testimonials</a><a href="#">Contact</a>
</nav>

<div class="abs hero" role="img" aria-label="Wedding party walking hand in hand along a beach at sunset"></div>

<main class="abs panel"></main>

<h2 style="left:68px;top:385px">Welcome</h2>
<div class="rule" style="left:60px;top:417px;width:505px"></div>
<p class="body-text" style="left:56px;top:430px;width:490px">Welcome to my services as a marriage celebrant in the Sydney area. I want people to have the impression I am a modern and professional marriage celebrant who can tailor a wedding ceremony and execute the ceremony with a high level of care and accommodate and adapt to any style of wedding and personalities of couples. I like a mint and pink and black theme I But would like to see ideas you can come up with Happy to use other photos you might have.</p>
<div class="photo welcome-photo" role="img" aria-label="Celebrant conducting a ceremony with the couple by the water"></div>

<h2 style="left:172px;width:506px;text-align:center;top:650px">Services</h2>
<div class="rule" style="left:172px;top:679px;width:506px"></div>
<div class="photo services-photo" role="img" aria-label="Couple holding hands with a bridal bouquet"></div>
<p class="body-text" style="left:172px;top:690px;width:535px">My services as a marriage celebrant in the Sydney area. I want people to have the impression I am a modern and professional marriage celebrant who can tailor a wedding ceremony and execute the ceremony with a high level of care and accommodate and adapt to any style of wedding and personalities of couples.<br><a class="read-more" href="#">Read More</a></p>

<h2 style="left:0;width:756px;text-align:center;top:855px">Tetimonials</h2>
<div class="rule" style="left:83px;top:889px;width:608px"></div>

<div class="avatar" style="left:60px;top:906px" role="img" aria-label="Portrait of a happy couple"></div>
<div class="client" style="left:57px;top:995px">Mr. / Mrs. A &amp; B</div>
<p class="quote" style="left:166px;top:935px">Ms. Mara Linwood is very professional<br>we are very happy</p>

<div class="avatar" style="left:425px;top:906px" role="img" aria-label="Portrait of a happy couple"></div>
<div class="client" style="left:422px;top:995px">Mr. / Mrs. A &amp; B</div>
<p class="quote" style="left:527px;top:935px">Ms. Mara Linwood is very professional<br>we are very happy</p>

<footer class="abs footer"></footer>
<ul class="footer-col" style="left:73px"><li>Home</li><li>About</li><li>Ceremony</li><li>Gallery</li></ul>
<ul class="footer-col" style="left:226px"><li>Contact</li><li>111-555-0142</li><li>Address: Sydney</li><li>Email: mara@email.com</li></ul>
<ul class="footer-col" style="left:461px"><li>Follow Us</li></ul>
<div class="social" aria-label="Social links"><span></span><span></span><span></span></div>
</body>
</html>
```